Home Remodeling company needs a business card design

we need a business card design for home remodeling company in hamilton county, indiana USA. we offers a wide range of construction services including whole house renovations, Design and Build Basements and Kitchen and Bathroom Remodeling . we would like to see designs for both site of business card that use the same color of the company logo and also including all information below :
1- Karim Feltous CEO / General Contractor
2- all company contacts Telephone numbers ( 1-888-DULOM-47 ) ( 317-555-0193) email address ( info@dulomhome.com) website ( www.dulomhome.com ) and social media logos (Facebook- twitter- google plus )
3- company logo
4- licensed . insured . bonded

```html
<!DOCTYPE html>
<html lang="en">
<head>
<meta charset="utf-8">
<title>Dulom Business Card</title>
<link rel="stylesheet" href="https://fonts.googleapis.com/css2?family=Cabin:wght@400;500;700&display=swap">
<style>
  :root {
    --bg: #e4e4e4;
    --card: #ffffff;
    --red: #c8303a;
    --ink: #3a3a3a;
    --ink-soft: #4a4a4a;
    --rule: #9a9a9a;
  }
  * { box-sizing: border-box; margin: 0; padding: 0; }
  html, body {
    width: 1105px; height: 1200px; overflow: hidden;
    background: var(--bg);
    font-family: "Cabin", sans-serif;
    color: var(--ink);
  }
  .card {
    position: absolute; left: 179px;
    width: 747px; height: 425px;
    background: var(--card);
  }
  .card--front { top: 120px; }
  .card--back { top: 655px; }

  /* front */
  .brand {
    position: absolute; left: 66px; top: 190px;
    width: 280px; text-align: center;
    font-weight: 700; font-size: 44px; letter-spacing: 4px;
    color: var(--ink); line-height: 1;
  }
  .divider {
    position: absolute; left: 387px; top: 117px;
    width: 2px; height: 180px; background: var(--rule);
  }
  .divider::before {
    content: ""; position: absolute; left: -1px; top: 0;
    width: 4px; height: 46px; background: var(--red);
  }
  .person { position: absolute; left: 435px; top: 106px; }
  .person__name { font-size: 30px; font-weight: 500; color: var(--ink); line-height: 1.1; }
  .person__title { font-size: 22px; color: var(--red); margin-top: 4px; }
  .contacts {
    position: absolute; left: 440px; top: 186px;
    list-style: none; font-size: 20px; color: var(--ink-soft);
  }
  .contacts li { display: flex; align-items: center; height: 29px; }
  .contacts svg { width: 18px; height: 18px; margin-right: 10px; fill: var(--ink); }
  .credentials {
    position: absolute; left: 0; right: 0; top: 362px;
    display: flex; justify-content: center; align-items: center; gap: 6px;
    font-size: 21px; color: var(--ink); letter-spacing: 0.3px;
  }
  .credentials__dot { width: 7px; height: 7px; background: var(--red); }

  /* back */
  .mark {
    position: absolute; left: 0; right: 0; top: 140px;
    display: flex; justify-content: center; align-items: center; gap: 16px;
    font-weight: 700; font-size: 56px; letter-spacing: 3px; color: var(--red); line-height: 1;
  }
  .mark__square { width: 56px; height: 56px; background: var(--red); }
  .tagline {
    position: absolute; left: 0; right: 0; top: 264px;
    text-align: center; font-size: 22px; color: var(--red);
  }
  .services {
    position: absolute; left: 0; right: 0; top: 308px;
    text-align: center; font-size: 18px; line-height: 24px; color: var(--ink);
  }
  .social {
    position: absolute; left: 0; right: 0; top: 362px;
    display: flex; justify-content: center; align-items: center; gap: 4px;
  }
  .social__rule { width: 62px; height: 1px; background: var(--rule); }
  .social__icon { width: 27px; height: 27px; border-radius: 50%; background: var(--ink); }
</style>
</head>
<body>
  <section class="card card--front">
    <div class="brand">DULOM</div>
    <div class="divider"></div>
    <div class="person">
      <p class="person__name">Karim Feltous</p>
      <p class="person__title">CEO / General Contractor</p>
    </div>
    <ul class="contacts">
      <li><svg viewBox="0 0 24 24"><path d="M6.6 10.8a15.1 15.1 0 0 0 6.6 6.6l2.2-2.2a1 1 0 0 1 1-.25 11.4 11.4 0 0 0 3.6.57 1 1 0 0 1 1 1V20a1 1 0 0 1-1 1A17 17 0 0 1 3 4a1 1 0 0 1 1-1h3.5a1 1 0 0 1 1 1c0 1.25.2 2.45.57 3.57a1 1 0 0 1-.25 1z"/></svg>1-888-DULOM-47</li>
      <li><svg viewBox="0 0 24 24"><path d="M7 1h10a2 2 0 0 1 2 2v18a2 2 0 0 1-2 2H7a2 2 0 0 1-2-2V3a2 2 0 0 1 2-2zm0 3v15h10V4z"/></svg>317-555-0193</li>
      <li><svg viewBox="0 0 24 24"><path d="M2 5h20v14H2zm2 2v.5l8 5 8-5V7l-8 5z"/></svg>info@dulomhome.com</li>
      <li><svg viewBox="0 0 24 24"><path d="M12 2a10 10 0 1 0 0 20 10 10 0 0 0 0-20zm0 2c1 0 2.3 2 2.8 5H9.2C9.7 6 11 4 12 4zM4.3 11h3.8a16 16 0 0 0 0 2H4.3a8 8 0 0 1 0-2zm11.6 0h3.8a8 8 0 0 1 0 2h-3.8a16 16 0 0 0 0-2zM9.2 15h5.6c-.5 3-1.8 5-2.8 5s-2.3-2-2.8-5z"/></svg>www.dulomhome.com</li>
    </ul>
    <div class="credentials">
      <span>LICENSED</span><span class="credentials__dot"></span>
      <span>INSURED</span><span class="credentials__dot"></span>
      <span>BONDED</span>
    </div>
  </section>

  <section class="card card--back">
    <div class="mark"><span class="mark__square"></span>DULOM</div>
    <p class="tagline">Quality Remodeling for Every Room of Your Home</p>
    <p class="services">Construction services | Whole house renovations<br>Design &amp; Build Basements | Kitchen &amp; Bathroom Remodeling</p>
    <div class="social">
      <span class="social__rule"></span>
      <span class="social__icon" role="img" aria-label="Social network link"></span>
      <span class="social__icon" role="img" aria-label="Social network link"></span>
      <span class="social__icon" role="img" aria-label="Social network link"></span>
      <span class="social__rule"></span>
    </div>
  </section>
</body>
</html>
```